TA BRAMLEY BUSINESS CARD DESIGN PROJECT

We need to utilize our logo that was expertly created on PixelHarbor and now need to match this with a business card design.

```html
<!DOCTYPE html>
<html lang="en">
<head>
<meta charset="utf-8">
<title>TA BRAMLEY Business Card</title>
<link href="https://fonts.googleapis.com/css2?family=Montserrat:wght@400;700;800&display=swap" rel="stylesheet">
<style>
  :root {
    --brand-blue: #0b3fa3;
    --card-white: #f4f4f3;
    --ink: #1d1d1f;
    --backdrop: #d6d6d6;
  }
  * { margin: 0; padding: 0; box-sizing: border-box; }
  html, body {
    width: 1200px; height: 1051px; overflow: hidden;
    background: var(--backdrop);
    font-family: "Montserrat", Arial, sans-serif;
  }
  .stage {
    width: 1200px; height: 1051px;
    display: flex; flex-direction: column; align-items: center; justify-content: center;
    gap: 50px;
  }
  .card {
    width: 700px; height: 400px;
    background: var(--card-white);
    border-bottom: 6px solid var(--brand-blue);
    border-left: 3px solid var(--brand-blue);
    box-shadow: 0 18px 40px rgba(0,0,0,0.18);
    position: relative;
  }
  .wordmark {
    display: flex; align-items: center; gap: 18px;
    color: var(--brand-blue);
    font-weight: 800; letter-spacing: 0.18em;
  }
  .wordmark__dot {
    width: 34px; height: 34px; border-radius: 50%;
    background: var(--brand-blue);
  }
  .card--front .wordmark {
    position: absolute; top: 70px; left: 0; right: 0; justify-content: center;
    font-size: 48px;
  }
  .card--back { display: flex; align-items: center; justify-content: center; }
  .card--back .wordmark { font-size: 64px; }
  .card--back .wordmark__dot { width: 46px; height: 46px; }
  .details {
    position: absolute; left: 0; right: 0; top: 210px;
    display: flex; justify-content: center; gap: 28px;
  }
  .details__person {
    text-align: right; font-size: 17px; line-height: 1.4; color: var(--ink);
  }
  .details__name {
    color: var(--brand-blue); font-weight: 700; font-size: 21px;
  }
  .details__rule { width: 2px; background: var(--brand-blue); }
  .details__contacts { list-style: none; font-size: 17px; line-height: 1.55; color: var(--ink); }
  .details__contacts li { display: flex; align-items: center; gap: 10px; }
  .details__contacts svg { width: 15px; height: 15px; fill: var(--brand-blue); flex: none; }
</style>
</head>
<body>
<main class="stage">
  <section class="card card--front">
    <div class="wordmark"><span class="wordmark__dot"></span>TA BRAMLEY</div>
    <div class="details">
      <div class="details__person">
        <p class="details__name">OWEN HARTLEY</p>
        <p>Managing Director</p>
        <p>Your address, City</p>
        <p>State, Zip 1234</p>
      </div>
      <div class="details__rule"></div>
      <ul class="details__contacts">
        <li><svg viewBox="0 0 16 16"><path d="M3 1l3 3-2 2c1 2 3 4 5 5l2-2 3 3-2 3C6 15 1 10 1 3z"/></svg>123 456 789</li>
        <li><svg viewBox="0 0 16 16"><rect x="3" y="1" width="10" height="14" rx="2"/></svg>123 456 789</li>
        <li><svg viewBox="0 0 16 16"><path d="M1 3h14v10H1z M1 3l7 6 7-6" /></svg>info@yourmail.com</li>
        <li><svg viewBox="0 0 16 16"><circle cx="8" cy="8" r="7"/></svg>www.yourwebsite.com</li>
      </ul>
    </div>
  </section>
  <section class="card card--back">
    <div class="wordmark"><span class="wordmark__dot"></span>TA BRAMLEY</div>
  </section>
</main>
</body>
</html>
```